Letter head / email signature/ contract document templates

We need a professional email signature and letterhead designed for our established carpentry and maintenance company. Our Logo (attached) was originally designed 6 years ago by design guru and we love it, looking for something to compliment it ( not a home job)

```html
<!DOCTYPE html>
<html lang="en">
<head>
<meta charset="utf-8">
<title>Coastline Trade Maintenance — Stationery</title>
<link rel="stylesheet" href="https://fonts.googleapis.com/css2?family=Arimo:wght@400&family=Lato:wght@400;700&display=swap">
<style>
  :root {
    --backdrop: #8b8b8d;
    --paper: #efeff0;
    --ink: #4a4a4c;
    --ink-dark: #333335;
    --brand-red: #d0111b;
    --rule: #555557;
  }
  * { margin: 0; padding: 0; box-sizing: border-box; }
  html, body { width: 1200px; height: 858px; overflow: hidden; }
  body { background: var(--backdrop); position: relative; font-family: "Lato", sans-serif; color: var(--ink); }

  .sheet { position: absolute; background: var(--paper); }

  .brand-name {
    display: flex; align-items: center; gap: 5px;
    font-family: "Lato", sans-serif; font-weight: 700;
    color: var(--ink-dark); line-height: 1.05; text-transform: uppercase; letter-spacing: 0.06em;
  }
  .brand-name .brand-square { width: 9px; height: 9px; background: var(--brand-red); flex: none; }

  /* Letterhead */
  .letterhead { left: 123px; top: 65px; width: 507px; height: 713px; }
  .letterhead .brand-name { position: absolute; left: 0; right: 0; top: 70px; justify-content: center; font-size: 15px; }
  .letter-greeting { position: absolute; left: 37px; top: 178px; font-family: "Arimo", sans-serif; font-size: 12px; color: var(--ink); }
  .letter-body { position: absolute; left: 37px; top: 216px; width: 433px; font-family: "Arimo", sans-serif; font-size: 7.3px; line-height: 10.8px; text-align: justify; color: var(--ink); }
  .letter-body p { margin-bottom: 10.8px; }
  .letter-closing { position: absolute; left: 37px; top: 455px; font-family: "Arimo", sans-serif; font-size: 7.5px; }
  .letter-signature { position: absolute; left: 33px; top: 478px; width: 148px; height: 42px; background: linear-gradient(90deg, #d8d8da, #e6e6e8); }
  .letter-footer { position: absolute; left: 113px; width: 280px; text-align: center; font-size: 7.3px; color: var(--ink); }
  .letter-footer.address-line { top: 661px; padding-bottom: 4px; border-bottom: 1px solid var(--rule); }
  .letter-footer.contact-line { top: 679px; left: 100px; width: 306px; }
  .letter-footer .label { color: var(--brand-red); }

  /* Business card */
  .business-card { left: 664px; top: 207px; width: 183px; height: 278px; }
  .business-card .brand-name { position: absolute; left: 22px; top: 44px; font-size: 10px; }
  .card-person { position: absolute; left: 22px; top: 141px; }
  .card-person .person-name { font-size: 13px; color: var(--brand-red); }
  .card-person .person-role { font-size: 9px; color: var(--ink-dark); margin-top: 1px; }
  .card-details { position: absolute; left: 22px; top: 183px; font-size: 8.7px; line-height: 11.3px; color: var(--ink); }

  .contact-list { list-style: none; }
  .contact-list li { display: flex; align-items: center; gap: 5px; white-space: nowrap; }
  .contact-list svg { width: 7px; height: 7px; flex: none; fill: var(--brand-red); }

  /* Email signature, wide */
  .signature-wide { left: 664px; top: 510px; width: 477px; height: 148px; }
  .signature-wide .brand-name { position: absolute; left: 80px; top: 66px; font-size: 11px; }
  .signature-wide .divider { position: absolute; left: 238px; top: 36px; width: 1px; height: 73px; background: #c4c4c6; }
  .signature-wide .sig-details { position: absolute; left: 259px; top: 39px; font-size: 8.7px; line-height: 11.3px; }

  /* Email signature, slim */
  .signature-slim { left: 662px; top: 680px; width: 477px; height: 92px; }
  .signature-slim .brand-name { position: absolute; left: 24px; top: 38px; font-size: 9px; }
  .signature-slim .divider { position: absolute; top: 25px; width: 1px; height: 40px; background: #c4c4c6; }
  .signature-slim .divider.first { left: 144px; }
  .signature-slim .divider.second { left: 313px; }
  .signature-slim .sig-contacts { position: absolute; left: 160px; top: 29px; font-size: 8.7px; line-height: 11.3px; }
  .signature-slim .sig-address { position: absolute; left: 329px; top: 31px; font-size: 8.7px; line-height: 11.3px; }
</style>
</head>
<body>
  <svg width="0" height="0" style="position:absolute">
    <defs>
      <symbol id="icon-phone" viewBox="0 0 10 10"><path d="M2 0.5l2 2-1 1.2c.6 1.3 1.6 2.3 2.9 2.9L7 5.5l2 2L7.8 9.3C4 9 1 6 0.7 2.2z"/></symbol>
      <symbol id="icon-mobile" viewBox="0 0 10 10"><path d="M2.5 0h5v10h-5zM3.6 1.2v6.8h2.8V1.2z"/></symbol>
      <symbol id="icon-mail" viewBox="0 0 10 10"><path d="M0 2h10v6H0zM1 3l4 3 4-3v4H1z"/></symbol>
      <symbol id="icon-globe" viewBox="0 0 10 10"><circle cx="5" cy="5" r="5"/></symbol>
    </defs>
  </svg>

  <section class="sheet letterhead">
    <div class="brand-name"><span class="brand-square"></span>Coastline Trade Maintenance</div>
    <p class="letter-greeting">Dear Mr. Harlow,</p>
    <div class="letter-body">
      <p>Lorem ipsum dolor sit amet, consectetur adipiscing elit. Donec orci purus, luctus vitae dignissim eu, iaculis sed purus. Vivamus faucibus, ipsum nec aliquet viverra, leo mauris condimentum ligula, sit amet sagittis enim ligula quis arcu. Nam egestas tortor id nisi porttitor mattis. In tortor ante, ultricies in suscipit a, tempus non massa. Vivamus et auctor mi. Fusce vel massa nulla. Phasellus nec eros mauris, et scelerisque orci.</p>
      <p>Donec malesuada orci vitae nulla accumsan porta a id massa. Quisque accumsan iaculis magna sit amet fringilla. Maecenas consequat, magna eget tincidunt semper, odio nibh rutrum mi, id feugiat ante nisi eu risus. Vestibulum nunc orci, rhoncus a placerat in, ultricies in mi. Cras mattis varius eros, vel fringilla nisi suscipit eget. Quisque scelerisque sagittis nulla at porttitor.</p>
      <p>Sed id augue vitae urna euismod commodo aliquet a quam. Pellentesque arcu velit, cursus et malesuada ut, consequat et diam. Nullam erat sem, rhoncus id ullamcorper vitae, rhoncus et arcu. In ultricies ultricies nulla, ut rutrum nisi iaculis at. Donec eu magna a metus ornare faucibus. Fusce aliquet faucibus ultricies. Morbi semper, est id tincidunt gravida, sem arcu adipiscing lacus, ac bibendum nulla leo eu purus. Quisque nec diam sed risus consectetur a ccumsan quis quis nibh. Vestibulum id purus lorem.</p>
      <p>It is a long established fact that a reader will be distracted by the readable content of a page when looking at its layout. The point of using Lorem Ipsum is that it has a more-or-less normal distribution of letters, as opposed to using 'Content here, content here', making it look like readable English. Many desktop publishing packages</p>
      <p>ada ut, consequat et diam. Nullam erat sem, rhoncus id ullamcorper vitae, rhoncus et arcu. In ultricies ultricies nulla, ut rutrum nisi iaculis at. Donec eu magna a metus ornare faucibus. Fusce aliquet faucibus ultricies. Morbi semper,</p>
    </div>
    <p class="letter-closing">Sincerely,</p>
    <div class="letter-signature" role="img" aria-label="Handwritten signature of the sender"></div>
    <p class="letter-footer address-line">1420 Fernwood Road, Riverton, Oregon 97010 | P. 555-014-2873</p>
    <p class="letter-footer contact-line"><span class="label">M.</span> 555-016-3390 <span class="label">E.</span> info@coastlinetrade.example <span class="label">W.</span> www.coastlinetrade.example</p>
  </section>

  <section class="sheet business-card">
    <div class="brand-name"><span class="brand-square"></span>Coastline Trade<br>Maintenance</div>
    <div class="card-person">
      <p class="person-name">Daniel Harlow</p>
      <p class="person-role">President</p>
    </div>
    <div class="card-details">
      <p>1420 Fernwood Road</p>
      <p style="margin-bottom:3px">Riverton, Oregon 97010</p>
      <ul class="contact-list">
        <li><svg><use href="#icon-phone"/></svg>555-014-2873</li>
        <li><svg><use href="#icon-mobile"/></svg>555-016-3390</li>
        <li><svg><use href="#icon-mail"/></svg>info@coastlinetrade.example</li>
        <li><svg><use href="#icon-globe"/></svg>www.coastlinetrade.example</li>
      </ul>
    </div>
  </section>

  <section class="sheet signature-wide">
    <div class="brand-name"><span class="brand-square"></span>Coastline Trade<br>Maintenance</div>
    <span class="divider"></span>
    <div class="sig-details">
      <p>1420 Fernwood Road</p>
      <p style="margin-bottom:3px">Riverton, Oregon 97010</p>
      <ul class="contact-list">
        <li><svg><use href="#icon-phone"/></svg>555-014-2873</li>
        <li><svg><use href="#icon-mobile"/></svg>555-016-3390</li>
        <li><svg><use href="#icon-mail"/></svg>info@coastlinetrade.example</li>
        <li><svg><use href="#icon-globe"/></svg>www.coastlinetrade.example</li>
      </ul>
    </div>
  </section>

  <section class="sheet signature-slim">
    <div class="brand-name"><span class="brand-square"></span>Coastline Trade<br>Maintenance</div>
    <span class="divider first"></span>
    <ul class="contact-list sig-contacts">
      <li><svg><use href="#icon-phone"/></svg>555-014-2873</li>
      <li><svg><use href="#icon-mobile"/></svg>555-016-3390</li>
      <li><svg><use href="#icon-mail"/></svg>info@coastlinetrade.example</li>
    </ul>
    <span class="divider second"></span>
    <div class="sig-address">
      <p>1420 Fernwood Road</p>
      <p>Riverton, Oregon 97010</p>
      <p>www.coastlinetrade.example</p>
    </div>
  </section>
</body>
</html>
```